Business Card Design

We would like to re-design our business cards. Our Company - Qwinrel Turbochargers, rebuilds turbochargers and sells replacement parts. Our website is: http://www.qwinrelturbochargers-example.com
We just had our logo changed. I will attach the file. Looking for fresh new/modern business card. We like the colors red, black, white and silver. Black background looks attractive, but not a requirement. The final design should communicate reasonable/competitive prices, top quality and reliability of our products.
Updates
Project Deadline Extended
Reason: Need to finalize the info on the card. Currently working on changing address and email info. Want to make sure it is the correct one before accepting the final design. Unless, this is something that can be changed at a later time..??
Industry/Entity Type
Business
Contact Information for Business Card
QWINREL TURBOCHARGERS, LLC
20473 Harwick Lane NE
Massillon, OH 44647
Tel: +1-555-214-7390
Fax: +1-555-267-1842
info@QwinrelTurbochargers-example.com
Our current business card had the following highlights:
*We rebuild all Turbocharges for Automotive, Diesel and Industrial
*Precision Balancing and in-house turbocharger needs
*All Turbocharger replacement parts are made in USA / U.K.
Look and feel
Each slider illustrates characteristics of the customer's brand and the style your logo design should communicate.

```html
<!DOCTYPE html>
<html lang="en">
<head>
<meta charset="utf-8">
<title>Qwinrel Turbochargers – Business Card</title>
<link href="https://fonts.googleapis.com/css2?family=Open+Sans:wght@400;600&display=swap" rel="stylesheet">
<style>
  :root {
    --bg: #e9e6e1;
    --red: #e3202b;
    --red-dark: #b5151e;
    --black: #121212;
    --charcoal: #262626;
    --white: #ffffff;
    --text-grey: #4a4a4a;
    --silver: #9a9a9a;
  }
  * { margin: 0; padding: 0; box-sizing: border-box; }
  html, body { width: 1200px; height: 1023px; overflow: hidden; }
  body {
    background: var(--bg);
    font-family: "Open Sans", Arial, sans-serif;
    position: relative;
  }
  .card {
    position: absolute;
    left: 250px;
    width: 700px;
    height: 400px;
    overflow: hidden;
    box-shadow: 0 6px 18px rgba(0,0,0,0.18);
  }
  .card-front { top: 70px; background: var(--white); }
  .card-back { top: 553px; background: var(--black); }
  .card-shape { position: absolute; inset: 0; width: 100%; height: 100%; }

  .front-content { position: absolute; left: 150px; top: 62px; }
  .brand-name {
    font-weight: 600;
    font-size: 30px;
    color: var(--charcoal);
    display: flex;
    align-items: center;
    gap: 12px;
    letter-spacing: 0.3px;
  }
  .brand-square { width: 18px; height: 18px; background: var(--red); display: inline-block; }
  .person { margin-top: 46px; }
  .person-name { font-size: 30px; color: var(--red); font-weight: 400; line-height: 1.1; }
  .person-title { font-size: 16px; color: var(--text-grey); margin-top: 4px; }
  .address { margin-top: 20px; font-size: 17px; color: var(--text-grey); line-height: 1.4; }
  .contacts { margin-top: 16px; list-style: none; font-size: 17px; color: var(--text-grey); line-height: 1.45; }
  .contacts li { display: flex; align-items: center; gap: 10px; }
  .contacts svg { width: 16px; height: 16px; flex: none; }

  .back-brand {
    position: absolute; left: 80px; top: 190px;
    font-weight: 600; font-size: 36px; color: var(--red);
    display: flex; align-items: center; gap: 14px;
  }
  .back-brand .brand-square { width: 22px; height: 22px; background: var(--silver); }
  .back-web {
    position: absolute; left: 80px; top: 250px;
    font-size: 18px; color: var(--silver);
  }
  .back-web .accent { color: var(--red); }
</style>
</head>
<body>
  <section class="card card-front" aria-label="Business card front">
    <svg class="card-shape" viewBox="0 0 700 400" aria-hidden="true">
      <rect width="700" height="400" fill="var(--red)"/>
      <path d="M110 0 H590 Q650 200 590 400 H110 Q50 200 110 0 Z" fill="var(--black)"/>
      <path d="M118 0 H582 Q640 200 582 400 H118 Q60 200 118 0 Z" fill="var(--white)"/>
    </svg>
    <div class="front-content">
      <div class="brand-name"><span class="brand-square"></span>Qwinrel Turbochargers</div>
      <div class="person">
        <div class="person-name">Corvin Ashdale</div>
        <div class="person-title">Director</div>
      </div>
      <div class="address">20473 Harwick Lane NE<br>Fenwick Falls, Ohio</div>
      <ul class="contacts">
        <li><svg viewBox="0 0 16 16"><path d="M4 1 L6.5 4.5 L5 6.5 Q6.5 9.5 9.5 11 L11.5 9.5 L15 12 L13 15 Q5 14 1 3 Z" fill="var(--red)"/></svg>+1-555-214-7390</li>
        <li><svg viewBox="0 0 16 16"><rect x="4" y="1" width="8" height="5" fill="var(--red)"/><rect x="1" y="6" width="14" height="7" rx="1" fill="var(--red)"/><rect x="4" y="10" width="8" height="5" fill="var(--white)" stroke="var(--red)"/></svg>+1-555-267-1842</li>
        <li><svg viewBox="0 0 16 16"><rect x="1" y="3" width="14" height="10" fill="var(--red)"/><path d="M1 3 L8 9 L15 3" stroke="var(--white)" stroke-width="1.3" fill="none"/></svg>info@QwinrelTurbochargers-example.com</li>
        <li><svg viewBox="0 0 16 16"><circle cx="8" cy="8" r="7" fill="var(--red)"/><path d="M1 8 H15 M8 1 Q3 8 8 15 M8 1 Q13 8 8 15" stroke="var(--white)" stroke-width="1" fill="none"/></svg>www.qwinrelturbochargers-example.com</li>
      </ul>
    </div>
  </section>

  <section class="card card-back" aria-label="Business card back">
    <svg class="card-shape" viewBox="0 0 700 400" aria-hidden="true">
      <rect width="700" height="400" fill="var(--black)"/>
      <path d="M480 0 L700 0 L700 400 L610 400 L660 230 L560 260 Z" fill="var(--charcoal)"/>
      <path d="M540 0 L640 0 L700 60 L700 300 L630 400 L600 400 L640 230 L545 250 L580 120 Z" fill="var(--red)"/>
    </svg>
    <div class="back-brand"><span class="brand-square"></span>Qwinrel Turbochargers</div>
    <div class="back-web">www.<span class="accent">qwinrelturbochargers-example</span>.com</div>
  </section>
</body>
</html>
```